QRV Advisors needs a web site

We need a web site for www.qrvadvisors-example.com. QRV is a mergers and acquisition consulting company that focuses our buyer and seller services on logistics companies. We help put companies together, and help with legal and financial due diligence. We want the web site to express our service and show the logistics components. We want personalized images versus pictures of trucks and airplanes.

Our new logo uses Burgandy and grey colors. Image attached. We are not in to bold, big letters...classy, artistic, low key preferred. Confidentiality, experience, professional are what we want to express on the site.

All we expect for the first part of this project is a home page, and one subpage.  We are budgeting other funds for the technical aspects of the web site

Reason: All that I'm seeing so far is trucks, forklifts and planes. We are a legal mergers and acquisitions firm that focus on logistics. I like some of the images to say logistics, but really want it say legal, financial, and putting companies together. Will pay extra for the sub page if someone can impress us with a home page.

Reason: Swamped with another project at the moment...will work on this over the weekend and provide designer feedback and select final design by Tuesday

```html
<!DOCTYPE html>
<html lang="en">
<head>
<meta charset="utf-8">
<title>QRV Advisors — Home</title>
<link rel="stylesheet" href="https://fonts.googleapis.com/css2?family=Ubuntu:wght@400;500&family=Open+Sans:wght@400;600;700&display=swap">
<style>
:root{
  --crimson:#b3093a;
  --crimson-dark:#8f0630;
  --crimson-light:#d0124a;
  --grey-text:#4a4a4a;
  --grey-mid:#6b6b6b;
  --grey-line:#d5d5d5;
  --panel:#f3f3f3;
  --white:#ffffff;
}
*{box-sizing:border-box;margin:0;padding:0}
html,body{width:1063px;height:1200px;overflow:hidden;background:var(--white);font-family:"Open Sans",Arial,sans-serif;color:var(--grey-text)}
.page{position:relative;width:1063px;height:1200px;overflow:hidden}
.top-band{position:absolute;left:0;top:0;width:1063px;height:407px;background:linear-gradient(#f8f8f8,#e4e4e4)}
.abs{position:absolute}

/* header */
.brand{left:141px;top:36px;display:flex;align-items:center;gap:12px}
.brand-mark{width:22px;height:22px;background:var(--crimson)}
.brand-name{font-family:"Ubuntu",sans-serif;font-weight:500;font-size:36px;color:var(--crimson);letter-spacing:1px}
.call{right:143px;top:43px;display:flex;align-items:center;gap:6px;font-family:"Ubuntu",sans-serif;font-size:17px;color:#555}
.call strong{font-weight:500;color:#333}

/* nav */
.nav{left:139px;top:105px;width:781px;height:33px;border-radius:3px;background:linear-gradient(var(--crimson-light),var(--crimson-dark));box-shadow:0 1px 0 #fff inset,0 2px 3px rgba(0,0,0,.25);display:flex;align-items:center;padding:0 8px}
.nav a{font-size:11px;font-weight:600;color:var(--white);text-decoration:none}
.nav a.current{background:var(--white);color:#555;border-radius:2px;padding:5px 13px;font-weight:600}
.nav .item{flex:1;text-align:center}

/* hero */
.hero{left:138px;top:152px;width:785px;height:311px;background:var(--white);border-radius:6px;box-shadow:0 4px 8px rgba(0,0,0,.25);padding:3px}
.hero-photo{width:779px;height:305px;border-radius:4px;background:
  linear-gradient(to bottom,rgba(0,0,0,0) 45%,rgba(40,42,46,.45) 100%),
  linear-gradient(100deg,#7a7d82 0%,#dde1e4 14%,#eef1f2 40%,#e6e9eb 62%,#b8bcc0 80%,#5e6166 100%)}
.hero-title{left:229px;top:184px;width:304px;text-align:center;font-family:"Ubuntu",sans-serif;font-weight:500;font-size:16.5px;line-height:23.5px;color:#555}
.hero-ctrl{left:762px;top:432px;width:105px;height:28px;background:linear-gradient(#fafafa,#e2e2e2);border-radius:4px 4px 0 0;display:flex}
.hero-ctrl span{flex:1;display:flex;align-items:center;justify-content:center;border-left:1px solid #ccc}
.hero-ctrl span:first-child{border-left:0}

/* panels */
.panel{background:linear-gradient(#f2f2f2,#fff);border:1px solid #e4e4e4;border-radius:3px}
.panel h2{font-family:"Ubuntu",sans-serif;font-weight:400;font-size:19px;color:#555;padding-bottom:7px;border-bottom:2px solid var(--crimson)}
.panel h2 em{font-style:normal;color:var(--crimson)}
.welcome{left:139px;top:490px;width:508px;height:190px;padding:7px 12px 0 12px}
.welcome h2{width:458px}
.welcome p{font-size:10.5px;line-height:15.2px;letter-spacing:.35px;margin-top:11px}
.more{font-size:10.5px;color:var(--crimson);text-decoration:underline}
.welcome .more{position:absolute;right:18px;top:170px}
.news{left:674px;top:490px;width:249px;height:190px;padding:7px 12px 0 12px}
.news-item{display:flex;gap:16px;padding:10px 0 9px 0;border-bottom:1px dotted #6c6cb0}
.date{width:37px;text-align:center;flex:none}
.date .m{background:var(--crimson);color:#fff;font-size:10px;font-weight:600;line-height:16px}
.date .d{background:#d6d6d6;color:#444;font-size:14px;font-weight:700;line-height:18px}
.news-item h3{font-size:11.5px;font-weight:600;color:var(--crimson);line-height:14px}
.news-item p{font-size:10px;color:#777;line-height:13.5px;margin-top:4px}
.news .more{position:absolute;right:16px;top:170px}

/* cards */
.card{top:697px;width:244px}
.card-photo{height:133px}
.card-bar{height:25px;background:linear-gradient(var(--crimson-light),var(--crimson-dark));display:flex;align-items:center;justify-content:space-between;color:#fff;font-family:"Ubuntu",sans-serif;font-weight:500;font-size:15px;padding-left:19px;box-shadow:0 4px 5px -3px rgba(0,0,0,.35)}
.card-bar .go{width:34px;height:25px;background:rgba(0,0,0,.12);display:flex;align-items:center;justify-content:center}
.card p{font-size:10.5px;line-height:16.3px;margin:11px 7px 0 7px}
.card ul{list-style:none;margin:12px 0 0 15px}
.card li{font-size:10.5px;line-height:16.3px}
.card li::before{content:"»";margin-right:7px;font-size:9px}
.card .more{position:absolute;right:4px;top:238px}

/* newsletter */
.newsletter{left:138px;top:963px;width:785px;height:36px;border:1px solid #ddd;border-radius:2px;background:#fafafa}
.nl-tag{left:0;top:0;height:34px;width:197px;background:var(--crimson);clip-path:polygon(0 0,90% 0,100% 50%,90% 100%,0 100%);display:flex;align-items:center;gap:10px;padding-left:10px;color:#fff;font-family:"Ubuntu",sans-serif;font-weight:500;font-size:16px}
.nl-text{left:207px;top:11px;font-size:10.5px;font-weight:600;color:#333}
.nl-input{left:547px;top:8px;width:163px;height:19px;background:#e3e3e3;border:1px solid #c8c8c8;font-size:10.5px;color:#444;padding:2px 7px}
.nl-submit{left:718px;top:8px;width:58px;height:19px;background:var(--crimson);color:#fff;font-size:11px;font-weight:700;text-align:center;line-height:19px}

/* footer */
.footer{left:0;top:1017px;width:1063px;height:183px;background:linear-gradient(var(--crimson),var(--crimson-dark));border-top:2px solid #6d0424;color:#fff}
.footer h4{font-family:"Ubuntu",sans-serif;font-weight:500;font-size:13.5px;padding-bottom:3px}
.quick{left:142px;top:15px;width:88px}
.quick h4{border-bottom:1px solid rgba(255,255,255,.25)}
.quick a{display:block;font-size:10.5px;font-weight:600;color:#fff;text-decoration:none;line-height:17.4px;margin-left:2px}
.locations{left:247px;top:15px}
.map{width:187px;height:115px;background:#e8e6de;border:2px solid #fff;margin-top:4px}
.contact{left:451px;top:15px;width:236px}
.contact h4{border-bottom:1px solid rgba(255,255,255,.25);width:155px}
.c-row{display:flex;gap:10px;align-items:flex-start;font-size:11px;line-height:14px;margin-top:13px;white-space:nowrap}
.c-row svg{flex:none;margin-top:1px}
.follow{left:760px;top:19px;display:flex;align-items:center;gap:8px;font-family:"Ubuntu",sans-serif;font-weight:500;font-size:14px}
.follow .sq{width:23px;height:23px;background:#e9e9e9;border-radius:3px;margin-left:1px}
.f-brand{left:682px;top:84px;width:242px;text-align:center;font-family:"Ubuntu",sans-serif;font-weight:500;font-size:30px;line-height:36px;color:#fff;letter-spacing:1px}
.copyright{left:682px;top:132px;width:242px;text-align:center;font-size:11.5px;line-height:15px}
</style>
</head>
<body>
<div class="page">
  <div class="top-band"></div>

  <header>
    <div class="abs brand"><span class="brand-mark"></span><span class="brand-name">QRV Advisors</span></div>
    <div class="abs call">
      <svg width="22" height="22" viewBox="0 0 22 22"><circle cx="11" cy="11" r="9.5" fill="none" stroke="#b3093a" stroke-width="1.6"/><path d="M8 6c-1.5 2.5-1.5 7.5 0 10l2-1.5c-.8-2-.8-5 0-7z" fill="#b3093a"/></svg>
      <span>Call us <strong>(010) 555-0147</strong></span>
    </div>
  </header>

  <nav class="abs nav">
    <span class="item" style="flex:.8"><a class="current" href="#">HOME</a></span>
    <span class="item"><a href="#">ABOUT US</a></span>
    <span class="item" style="flex:1.2"><a href="#">BUYER SERVICES</a></span>
    <span class="item" style="flex:1.2"><a href="#">SELLER SERVICES</a></span>
    <span class="item" style="flex:1.2"><a href="#">NEWS &amp; EVENTS</a></span>
    <span class="item" style="flex:.8"><a href="#">FAQ's</a></span>
    <span class="item"><a href="#">CONTACT US</a></span>
  </nav>

  <section class="abs hero">
    <div class="hero-photo" role="img" aria-label="Executive presenting to a team seated around a glass boardroom table"></div>
  </section>
  <div class="abs hero-title">QRV Services Are Offered By Industry Executives With Extensive M&amp;A Experience</div>
  <div class="abs hero-ctrl">
    <span><svg width="24" height="10"><path d="M2 2l10 6 10-6" fill="none" stroke="#888" stroke-width="1.3"/></svg></span>
    <span><svg width="24" height="10"><path d="M2 8l10-6 10 6" fill="none" stroke="#888" stroke-width="1.3"/></svg></span>
  </div>

  <section class="abs panel welcome">
    <h2>Welcome to QRV <em>Advisors</em></h2>
    <p>QRV assists business owners within the logistics industry to implement growth and exit strategies. We offer business planning and merger and acquisition(M&amp;A) advisory services. QRV services are offered by industry executives with extensive M&amp;A experience. Your company will benefit from a unique and outside perspective from consultants that understand your business.</p>
    <p>QRV can help you formulate and execute your growth strategy. We take a strategic and consultative approach with our advisory services ...</p>
    <a class="more" href="#">Read More »</a>
  </section>

  <section class="abs panel news">
    <h2>News/Events</h2>
    <div class="news-item">
      <div class="date"><div class="m">MAR</div><div class="d">29</div></div>
      <div><h3>Duis aute irure reprehenderit</h3><p>Lorem consectetur adipiscing elit. Morbi tristique sem.</p></div>
    </div>
    <div class="news-item">
      <div class="date"><div class="m">APR</div><div class="d">01</div></div>
      <div><h3>Duis aute irure reprehenderit</h3><p>Lorem consectetur adipiscing elit. Morbi tristique sem.</p></div>
    </div>
    <a class="more" href="#">Read More »</a>
  </section>

  <article class="abs card" style="left:142px">
    <div class="card-photo" role="img" aria-label="Business partners shaking hands across a meeting table" style="background:linear-gradient(#d9d4cc,#5b5e66)"></div>
    <div class="card-bar">What We Do<span class="go"><svg width="11" height="10"><path d="M0 3.5h5V0l6 5-6 5V6.5H0z" fill="#fff"/></svg></span></div>
    <p>Lorem consectetur adipiscing elit. Morbi tristique sem. Nunc nec ipsum sed nisi Morbi tristique sem.Lorem consectetur adipiscing elit consectetur adi pis cing elit.</p>
    <a class="more" href="#">Read More »</a>
  </article>

  <article class="abs card" style="left:406px">
    <div class="card-photo" role="img" aria-label="Advisory team reviewing charts in an office meeting" style="background:linear-gradient(#9aa8b5,#2e333b)"></div>
    <div class="card-bar">Our Services<span class="go"><svg width="11" height="10"><path d="M0 3.5h5V0l6 5-6 5V6.5H0z" fill="#fff"/></svg></span></div>
    <ul><li>Business Analysis</li><li>Business Intelligence</li><li>Mergers</li><li>Acquisition</li></ul>
    <a class="more" href="#">Read More »</a>
  </article>

  <article class="abs card" style="left:671px">
    <div class="card-photo" role="img" aria-label="Figures navigating a large maze toward a goal" style="background:linear-gradient(#c8c8c8,#6f6f6f)"></div>
    <div class="card-bar">Our Mission<span class="go"><svg width="11" height="10"><path d="M0 3.5h5V0l6 5-6 5V6.5H0z" fill="#fff"/></svg></span></div>
    <p>Lorem consectetur adipiscing elit. Morbi tristique sem. Nunc nec ipsum sed nisi Morbi tristique sem.Lorem consectetur adipiscing elit consectetur ad ipis cing elit.</p>
    <a class="more" href="#">Read More »</a>
  </article>

  <section class="abs newsletter">
    <div class="abs nl-tag">
      <svg width="17" height="17" viewBox="0 0 17 17"><path d="M10 2H2v13h12V8" fill="none" stroke="#fff" stroke-width="1.6"/><path d="M7 11l1-3 7-7 2 2-7 7z" fill="#fff"/></svg>
      Newsletter Signup
    </div>
    <div class="abs nl-text">Lorem ipsum doloronsectetur adipiscing elit. Morbi id tristique.</div>
    <div class="abs nl-input">Email address</div>
    <div class="abs nl-submit">SUBMIT</div>
  </section>

  <footer class="abs footer">
    <div class="abs quick">
      <h4>Quick Link</h4>
      <a href="#">Home</a><a href="#">About Us</a><a href="#">Buyer Services</a><a href="#">Seller Services</a><a href="#">News &amp; Events</a><a href="#">FAQ's</a><a href="#">Contact us</a>
    </div>
    <div class="abs locations">
      <h4>QRV Locations</h4>
      <div class="map" role="img" aria-label="Street map showing the office location"></div>
    </div>
    <div class="abs contact">
      <h4>Contact Us</h4>
      <div class="c-row"><svg width="18" height="16" viewBox="0 0 18 16"><path d="M1 8L9 1l8 7M4 6v9h4v-5h2v5h4V6" fill="none" stroke="#fff" stroke-width="1.6"/></svg><span>Lorem consectetur adipiscing<br>elit. Morbi tristique sem.</span></div>
      <div class="c-row"><svg width="18" height="16" viewBox="0 0 18 16"><circle cx="8" cy="8" r="7" fill="none" stroke="#fff" stroke-width="1.4"/><path d="M6 4c-1.2 2-1.2 6 0 8l1.6-1.2c-.6-1.6-.6-4 0-5.6z" fill="#fff"/></svg><span>(010) 555-0147</span></div>
      <div class="c-row"><svg width="18" height="16" viewBox="0 0 18 16"><rect x="4" y="1" width="9" height="4" fill="#fff"/><rect x="1" y="5" width="16" height="7" rx="1" fill="#fff"/><rect x="4" y="10" width="9" height="5" fill="#fff" stroke="#b3093a"/></svg><span>(010) 555-0147</span></div>
      <div class="c-row"><svg width="18" height="14" viewBox="0 0 18 14"><rect x="1" y="2" width="16" height="10" fill="#fff"/><path d="M1 2l8 6 8-6" fill="none" stroke="#b3093a" stroke-width="1.2"/></svg><span>contact@qrvadvisors-example.com</span></div>
    </div>
    <div class="abs follow">Follow Us: <span class="sq"></span><span class="sq"></span><span class="sq"></span></div>
    <div class="abs f-brand">QRV Advisors</div>
    <div class="abs copyright">© 2014 QRV ADVISORS.<br>All rights reserved.</div>
  </footer>
</div>
</body>
</html>
```